Pharmacy ad

need 2 pharmacy ads for the phone book. one for Brookvale Pharmacy and one for Cedarline Care Pharmacy. Dimensions for ad is 4.75in x 4.667 in. please see attached examples of ad uploaded as well logos of each pharmacy

```html
<!DOCTYPE html>
<html lang="en">
<head>
<meta charset="utf-8">
<title>Pharmacy Ads</title>
<link rel="stylesheet" href="https://fonts.googleapis.com/css2?family=Barlow+Semi+Condensed:wght@600;700&family=Montserrat:wght@400;600;700&family=Dosis:wght@400;500;600&family=Kaushan+Script&display=swap">
<style>
  :root {
    --backdrop: #fdf0a6;
    --navy: #1c2251;
    --red: #e0262b;
    --sky: #bfe2f2;
    --sky-deep: #6fb8dc;
    --leaf: #7cc242;
    --leaf-light: #cfe59a;
    --leaf-pale: #e3f0cc;
    --brand-blue: #3b4ea6;
    --social: #3b5998;
    --white: #ffffff;
  }
  * { box-sizing: border-box; margin: 0; padding: 0; }
  html, body { width: 1200px; height: 600px; overflow: hidden; }
  body { background: var(--backdrop); position: relative; font-family: "Montserrat", sans-serif; color: var(--navy); }
  .ad { position: absolute; top: 22px; width: 567px; height: 556px; overflow: hidden; box-shadow: 2px 3px 6px rgba(0,0,0,.25); }
  .ad > * { position: absolute; }
  .ad-brookvale { left: 19px; background: var(--sky); border: 2px solid var(--navy); }
  .ad-cedarline { left: 612px; width: 568px; background: var(--white); border: 1px solid var(--leaf); }
  .bg-shapes { left: 0; top: 0; width: 100%; height: 100%; }
  .line { white-space: nowrap; line-height: 1; }

  /* Brookvale */
  .offer-block { left: 0; width: 266px; text-align: center; }
  .offer-pct { font-weight: 700; color: var(--red); font-size: 40px; }
  .offer-light { font-weight: 400; font-size: 20px; }
  .offer-bold { font-weight: 700; font-size: 20px; }
  .dot-rule { border-top: 3px dotted var(--navy); }
  .brand-name { left: 300px; width: 250px; text-align: center; font-family: "Barlow Semi Condensed", sans-serif; font-weight: 700; font-size: 42px; color: var(--navy); letter-spacing: 1px; }
  .brand-mark { border-radius: 50%; background: var(--leaf); }
  .tagline { left: 300px; width: 250px; text-align: center; font-style: italic; font-size: 13px; color: #4fa33a; }
  .pay-badge { background: var(--white); border-radius: 2px; display: flex; align-items: center; justify-content: center; font-size: 8px; font-weight: 700; color: var(--navy); box-shadow: 0 0 2px rgba(0,0,0,.3); }
  .service-list { list-style: none; font-weight: 700; font-size: 10.5px; line-height: 1.15; }
  .service-list li { position: absolute; left: 0; white-space: nowrap; }
  .service-list li::before { content: "\25C6"; font-size: 7px; margin-right: 4px; vertical-align: 2px; }
  .hours { font-weight: 700; font-size: 20px; color: var(--navy); }
  .address { font-size: 13px; font-weight: 400; display: flex; align-items: center; gap: 5px; }
  .phone { font-size: 13px; font-weight: 400; letter-spacing: 1px; display: flex; align-items: center; gap: 5px; }
  .small-note { font-size: 10px; }
  .visit { font-size: 13px; text-align: center; width: 90px; }
  .social-dot { border-radius: 50%; background: var(--social); }
  .social-name { font-size: 9px; text-align: center; width: 90px; font-weight: 600; }

  /* Cedarline */
  .cedar-name { font-family: "Dosis", sans-serif; font-weight: 600; color: var(--brand-blue); font-size: 34px; line-height: 1; }
  .accept-label { font-weight: 700; font-size: 11px; }
  .slogan { left: 0; width: 100%; text-align: center; font-family: "Kaushan Script", cursive; font-size: 42px; color: var(--brand-blue); line-height: 1; }
  .cedar-pct { font-family: "Barlow Semi Condensed", sans-serif; font-weight: 700; color: var(--red); font-size: 62px; line-height: 1; }
  .cedar-label { font-family: "Dosis", sans-serif; color: var(--brand-blue); line-height: 1; }
  .cedar-list { list-style: none; font-family: "Dosis", sans-serif; font-size: 14px; font-weight: 500; color: var(--brand-blue); line-height: 1.05; }
  .cedar-list li { position: absolute; left: 0; white-space: nowrap; padding-left: 9px; }
  .cedar-list li::before { content: "\2022"; position: absolute; left: 0; }
  .divider { width: 3px; background: var(--leaf); }
  .footer-hours { font-weight: 700; font-size: 17px; color: var(--navy); }
  .footer-info { font-weight: 600; font-size: 11.5px; display: flex; align-items: center; gap: 5px; }
  .icon { width: 12px; height: 12px; flex: none; }
</style>
</head>
<body>

<section class="ad ad-brookvale" aria-label="Brookvale Pharmacy advertisement">
  <svg class="bg-shapes" viewBox="0 0 567 556" preserveAspectRatio="none" aria-hidden="true">
    <defs>
      <linearGradient id="shelfTone" x1="0" y1="0" x2="1" y2="1">
        <stop offset="0" stop-color="#e6f3fa"/>
        <stop offset="0.5" stop-color="#c4e3f2"/>
        <stop offset="1" stop-color="#9fd0e8"/>
      </linearGradient>
      <linearGradient id="leafTone" x1="0" y1="0" x2="1" y2="1">
        <stop offset="0" stop-color="#a6d36a"/>
        <stop offset="1" stop-color="#d3e8a4"/>
      </linearGradient>
    </defs>
    <rect x="0" y="0" width="567" height="556" fill="url(#shelfTone)" role="img" aria-label="Softly blurred pharmacy shelves"/>
    <path d="M0 0 H285 C340 80 345 200 300 262 H0 Z" fill="#a9d6ec" opacity="0.75"/>
    <circle cx="430" cy="200" r="150" fill="#ffffff" opacity="0.45"/>
    <path d="M330 288 C450 288 540 300 567 312 V560 H330 Z" fill="#5fb0da"/>
    <path d="M0 262 H300 C420 262 520 340 567 470 V556 H0 Z" fill="url(#leafTone)"/>
  </svg>

  <div class="offer-block" style="top:22px"><p class="line offer-pct">10%</p></div>
  <div class="offer-block" style="top:62px"><p class="line offer-light">SENIOR CITIZEN</p></div>
  <div class="offer-block" style="top:82px"><p class="line offer-light">DISCOUNT</p></div>
  <div class="offer-block" style="top:102px"><p class="line offer-bold">FOR PATIENTS 60</p></div>
  <div class="offer-block" style="top:122px"><p class="line offer-bold">YEARS AND OVER</p></div>
  <div class="dot-rule" style="left:70px;top:152px;width:126px"></div>
  <div class="offer-block" style="top:168px"><p class="line offer-pct">10%</p></div>
  <div class="offer-block" style="top:208px"><p class="line offer-light">STUDENT DISCOUNT</p></div>
  <div class="offer-block" style="top:228px"><p class="line offer-bold">WITH VALID ID CARD</p></div>

  <div class="brand-mark" style="left:395px;top:40px;width:62px;height:62px"></div>
  <p class="line brand-name" style="top:157px">BROOKVALE</p>
  <p class="line brand-name" style="top:198px">PHARMACY</p>
  <p class="line tagline" style="top:250px">We Care About Your Health</p>

  <div class="pay-badge" style="left:371px;top:309px;width:48px;height:32px">Paylink</div>
  <div class="pay-badge" style="left:434px;top:309px;width:49px;height:32px">Ringcard</div>
  <div class="pay-badge" style="left:498px;top:309px;width:44px;height:32px">Shoreline</div>
  <div class="pay-badge" style="left:399px;top:349px;width:116px;height:24px">Harborline Insurance</div>

  <ul class="service-list" style="left:37px;top:278px">
    <li style="top:0">Certified Pharmacists</li>
    <li style="top:22px">Affordable prices</li>
    <li style="top:44px">Brand and Generic<br>&nbsp;&nbsp;&nbsp;&nbsp;Medicines</li>
    <li style="top:80px">Blood Pressure and<br>&nbsp;&nbsp;&nbsp;&nbsp;Glucose checks</li>
  </ul>
  <ul class="service-list" style="left:180px;top:278px">
    <li style="top:0">Personal care and<br>&nbsp;&nbsp;&nbsp;&nbsp;Beauty Products</li>
    <li style="top:36px">Injectables</li>
    <li style="top:62px">Special Orders</li>
    <li style="top:88px">Delivery service</li>
  </ul>
  <div class="dot-rule" style="left:26px;top:386px;width:348px;border-top-width:2px"></div>
  <p class="line" style="left:26px;top:398px;font-size:12px">For more inquiries, email us: hello@brookvalerx.com</p>

  <p class="line hours" style="left:26px;top:418px">MONDAY – SATURDAY 9AM TO 5PM</p>
  <div class="line address" style="left:26px;top:440px">
    <svg class="icon" viewBox="0 0 12 12" aria-hidden="true"><path d="M6 0a4 4 0 0 1 4 4c0 3-4 8-4 8S2 7 2 4a4 4 0 0 1 4-4z" fill="currentColor"/><circle cx="6" cy="4" r="1.5" fill="#cfe59a"/></svg>
    Harbour Walk, Food Court, Easton
  </div>
  <div class="line phone" style="left:300px;top:440px">
    <svg class="icon" viewBox="0 0 12 12" aria-hidden="true"><path d="M1 4c0-2 2-3 5-3s5 1 5 3v1H8V4H4v1H1z M2 6h8l1 5H1z" fill="currentColor"/></svg>
    555-0177
  </div>
  <p class="line hours" style="left:28px;top:463px">MONDAY – FRIDAY 10AM TO 6PM,</p>
  <p class="line hours" style="left:28px;top:485px">SAT 10AM TO 5PM &amp; SUN 10AM TO 2PM</p>
  <div class="line address" style="left:26px;top:509px">
    <svg class="icon" viewBox="0 0 12 12" aria-hidden="true"><path d="M6 0a4 4 0 0 1 4 4c0 3-4 8-4 8S2 7 2 4a4 4 0 0 1 4-4z" fill="currentColor"/><circle cx="6" cy="4" r="1.5" fill="#cfe59a"/></svg>
    19 Kestrel Street, Easton
  </div>
  <p class="line small-note" style="left:40px;top:524px">(opposite Grace Hill Chapel)</p>
  <div class="line phone" style="left:300px;top:507px">
    <svg class="icon" viewBox="0 0 12 12" aria-hidden="true"><path d="M1 4c0-2 2-3 5-3s5 1 5 3v1H8V4H4v1H1z M2 6h8l1 5H1z" fill="currentColor"/></svg>
    555-0174
  </div>

  <p class="line visit" style="left:460px;top:462px">Visit us on</p>
  <div class="social-dot" style="left:485px;top:481px;width:40px;height:40px"></div>
  <p class="line social-name" style="left:460px;top:526px">Linkspace</p>
</section>

<section class="ad ad-cedarline" aria-label="Cedarline Care Pharmacy advertisement">
  <svg class="bg-shapes" viewBox="0 0 568 556" preserveAspectRatio="none" aria-hidden="true">
    <defs>
      <linearGradient id="photoTone" x1="0" y1="0" x2="1" y2="0">
        <stop offset="0" stop-color="#f4f6f8"/>
        <stop offset="0.5" stop-color="#e4e8ec"/>
        <stop offset="0.8" stop-color="#c9b6a6"/>
        <stop offset="1" stop-color="#e9ecef"/>
      </linearGradient>
    </defs>
    <rect x="0" y="0" width="568" height="215" fill="url(#photoTone)" role="img" aria-label="Pharmacist in a white coat holding a medicine bottle"/>
    <rect x="0" y="190" width="568" height="140" fill="#e3f0cc"/>
    <path d="M0 165 C180 200 400 210 568 160 V200 C400 235 180 225 0 205 Z" fill="#3b4ea6"/>
    <path d="M0 180 C180 215 400 220 568 175 V215 C400 245 180 240 0 225 Z" fill="#7cc242"/>
    <path d="M0 195 C180 230 400 235 568 195 V240 C400 260 180 255 0 240 Z" fill="#e3f0cc"/>
    <path d="M0 290 C200 270 380 275 568 305 V335 H0 Z" fill="#3b4ea6"/>
    <path d="M0 298 C200 280 380 285 568 313 V446 H0 Z" fill="#ffffff"/>
    <rect x="0" y="446" width="568" height="110" fill="#7cc242"/>
  </svg>

  <div class="brand-mark" style="left:40px;top:36px;width:56px;height:56px;background:var(--brand-blue)"></div>
  <p class="cedar-name" style="left:110px;top:30px">Cedarline Care</p>
  <p class="cedar-name" style="left:110px;top:66px">Pharmacy</p>

  <p class="line accept-label" style="left:78px;top:129px">WE ACCEPT:</p>
  <div class="pay-badge" style="left:80px;top:145px;width:42px;height:27px">Paylink</div>
  <div class="pay-badge" style="left:132px;top:145px;width:42px;height:27px">Ringcard</div>
  <div class="pay-badge" style="left:184px;top:145px;width:36px;height:27px;font-size:7px">Shoreline</div>
  <div class="pay-badge" style="left:226px;top:150px;width:114px;height:20px">Harborline Insurance</div>

  <p class="slogan" style="top:225px">Where good health begins</p>

  <p class="cedar-pct" style="left:30px;top:314px">10%</p>
  <p class="cedar-label line" style="left:134px;top:322px;font-size:16px">SENIOR CITIZEN</p>
  <p class="cedar-label line" style="left:134px;top:340px;font-size:24px">DISCOUNT</p>
  <p class="cedar-pct" style="left:30px;top:370px">10%</p>
  <p class="cedar-label line" style="left:134px;top:376px;font-size:16px">STUDENT</p>
  <p class="cedar-label line" style="left:134px;top:391px;font-size:24px">DISCOUNT</p>
  <p class="cedar-label line" style="left:134px;top:412px;font-size:10px;font-weight:600">(WITH VALID ID CARD)</p>

  <div class="divider" style="left:274px;top:321px;height:107px"></div>

  <ul class="cedar-list" style="left:290px;top:322px">
    <li style="top:0">Certified Pharmacists</li>
    <li style="top:20px">Affordable prices</li>
    <li style="top:40px">Brand and<br>Generic Medicines</li>
    <li style="top:76px">Blood Pressure and<br>Glucose checks</li>
  </ul>
  <ul class="cedar-list" style="left:426px;top:322px">
    <li style="top:0">Personal care and<br>Beauty Products</li>
    <li style="top:34px">Injectables</li>
    <li style="top:58px">Special Orders</li>
    <li style="top:82px">Delivery service</li>
  </ul>

  <p class="line footer-hours" style="left:30px;top:457px">MONDAY – SATURDAY 8AM TO 7PM</p>
  <p class="line footer-hours" style="left:30px;top:477px">SUNDAY 10AM TO 2PM</p>
  <div class="line footer-info" style="left:30px;top:504px">
    <svg class="icon" viewBox="0 0 12 12" aria-hidden="true"><path d="M6 0a4 4 0 0 1 4 4c0 3-4 8-4 8S2 7 2 4a4 4 0 0 1 4-4z" fill="#3b4ea6"/><circle cx="6" cy="4" r="1.5" fill="#7cc242"/></svg>
    Unit C1, Crown Pavilion Hotel, Bay Road, Easton
  </div>
  <div class="line footer-info" style="left:30px;top:523px">
    <svg class="icon" viewBox="0 0 12 12" aria-hidden="true"><rect x="0.5" y="2" width="11" height="8" fill="#3b4ea6"/><path d="M0.5 2 L6 7 L11.5 2" stroke="#7cc242" stroke-width="1" fill="none"/></svg>
    care@cedarlinerx.com
  </div>
  <div class="line footer-info" style="left:260px;top:523px;font-size:13px">
    <svg class="icon" viewBox="0 0 12 12" aria-hidden="true"><path d="M1 4c0-2 2-3 5-3s5 1 5 3v1H8V4H4v1H1z M2 6h8l1 5H1z" fill="#3b4ea6"/></svg>
    555-0155
  </div>

  <p class="line visit" style="left:455px;top:457px;color:var(--brand-blue)">Visit us on</p>
  <div class="social-dot" style="left:479px;top:478px;width:42px;height:42px"></div>
  <p class="line social-name" style="left:455px;top:526px">Linkspace</p>
</section>

</body>
</html>
```